Webdesign für Full-Service-Internetagentur
Zielgruppe
Falkenhainer Webdesign – Ihr Partner für außergewöhnliche Onlinepräsenzen
Wir bieten seit mehr als 16 Jahren Internetauftritte für kleine und mittelständische Unternehmen an.
Als Full-Service-Internetagentur liefern wir Ihnen individuelle auf Ihre Bedürfnisse, Ihre Branche und Ihre Zielgruppe zugeschnittene Lösungen für Ihre Onlinepräsentation an. Unser Angebot beinhaltet sowohl ein ideenreiches Webdesign kombiniert mit den aktuellsten Grundsätzen für Web-Programmierung als auch die Unterstützung für Ihr erfolgreiches Werben im Internet.
Eine gute Beratung heißt für uns genau hinhören und verstehen, was Sie wirklich brauchen. Je besser wir Ihre Ziele kennen, desto besser können wir Ihre Onlinepräsenz umsetzen. Unsere Kundenberater erläutern Ihnen persönlich mit Enthusiasmus die verschiedenen Möglichkeiten der Darstellung Ihrer Firma im Internet und entwickeln Konzepte, die Ihren Anforderungen bestmöglich entsprechen. Nicht nur während der Projektphase, sondern auch nach Onlinestellung Ihrer Internetseite stehen wir Ihnen mit persönlicher Kundenbetreuung und Supportdienstleistungen zur Verfügung.
Aufgabenstellung
siehe : https://www.falkenhainer-webdesign.example/

```html
<!DOCTYPE html>
<html lang="de">
<head>
<meta charset="utf-8">
<title>Falkenhainer Webdesign – Ideen, die Kreise ziehen</title>
<link href="https://fonts.googleapis.com/css2?family=Open+Sans:wght@400;600;700&display=swap" rel="stylesheet">
<style>
:root{
  --red:#d81f2a;
  --ink:#2b2b2b;
  --text:#444;
  --muted:#777;
  --hero-bg:#f4f5f9;
  --footer-bg:#f6f7fa;
  --line:#e3e3e8;
  --tile-blue:#afe1fc;
  --tile-orange:#ee7f00;
  --tile-sand:#efb866;
  --tile-navy:#2b2a5c;
  --tile-lilac:#c39ad6;
}
*{box-sizing:border-box;margin:0;padding:0}
html,body{width:1200px;height:2909px;overflow:hidden}
body{position:relative;background:#fff;font-family:"Open Sans",Arial,sans-serif;color:var(--text)}
.abs{position:absolute}
a{color:inherit}

.hero{left:0;top:0;width:1200px;height:436px;background:var(--hero-bg)}
.nav{left:88px;top:52px;display:flex;gap:29px;font-size:13px;font-weight:600;color:var(--ink)}
.nav .active{color:var(--red);border-bottom:3px solid var(--red);padding-bottom:3px}
.social{left:896px;top:58px;display:flex;gap:20px;align-items:center}
.social span{width:8px;height:8px;border-radius:50%;background:var(--ink);display:block}
.phone-top{left:1021px;top:52px;font-size:13px;font-weight:600;color:var(--ink);text-decoration:underline}
.brand{left:0;top:165px;width:1200px;text-align:center;font-size:50px;font-weight:600;color:var(--ink);letter-spacing:-.5px}
.tagline{left:0;top:243px;width:1200px;text-align:center;font-size:27px;color:var(--ink)}

.service{top:423px;width:243px;height:177px;background:#fff;border-radius:8px;box-shadow:0 4px 14px rgba(0,0,0,.06);text-align:center;padding:36px 18px 0}
.service h3{font-size:16px;font-weight:400;color:var(--red);line-height:22px;margin-bottom:12px}
.service p{font-size:13px;line-height:18px;color:#555}

.section-title{left:88px;font-size:27px;font-weight:400;color:var(--red);line-height:40px}
.rule{left:88px;height:5px;background:var(--red);border-radius:3px}

.lead{left:88px;top:791px;font-size:18px;color:var(--ink)}
.body-copy{left:88px;width:1024px;font-size:10px;line-height:16px;color:#555}
.body-copy a{color:var(--red)}

.tile{display:flex;align-items:center;justify-content:center;text-align:center;border-radius:3px;box-shadow:0 3px 10px rgba(0,0,0,.08)}
.tile-name{font-family:"Open Sans",Arial,sans-serif}
.badge{left:30px;top:28px;background:var(--red);color:#fff;font-size:9px;font-weight:700;padding:3px 14px;border-radius:6px}

.carousel{left:88px;top:1698px;display:flex;align-items:center;gap:6px}
.dot{width:7px;height:5px;border-radius:3px;background:#f0c8cb}
.dot.on{width:12px;background:var(--red)}

.news{top:1876px;height:135px;background:#fff;box-shadow:0 3px 12px rgba(0,0,0,.08);padding:20px 20px 0 30px}
.news time{display:block;font-size:8px;color:#aaa;margin-bottom:2px}
.news h4{font-size:12.5px;font-weight:400;color:var(--ink);line-height:17px;margin-bottom:7px;white-space:nowrap}
.news h4.wrap{white-space:normal}
.news p{font-size:8.5px;line-height:13px;color:#555;margin-bottom:7px}
.news a{font-size:8px;color:var(--red)}

.kicker{left:88px;top:2185px;font-size:11px;font-weight:600;color:var(--ink);display:flex;align-items:center;gap:10px}
.kicker::before{content:"";width:18px;height:1px;background:var(--ink)}
.form-title{left:116px;top:2204px;font-size:29px;color:var(--ink)}
.form-intro{left:88px;top:2252px;width:310px;font-size:12px;line-height:17px;color:#555}
.field{left:88px;width:304px;height:28px;border:1px solid #ddd;border-radius:14px;font-size:9px;color:#999;padding:8px 16px}
.submit{left:88px;top:2612px;width:304px;height:24px;background:var(--red);border-radius:12px;color:#fff;font-size:9px;font-weight:700;text-align:center;line-height:24px;box-shadow:0 3px 8px rgba(216,31,42,.3)}

.map{left:533px;top:2181px;width:578px;height:290px;background:linear-gradient(135deg,#f1f1f1,#e4e4e4 55%,#eeeeee);box-shadow:0 6px 18px rgba(0,0,0,.08)}
.info{display:flex;gap:12px;align-items:flex-start;font-size:10px;line-height:15px;color:#444}
.info .ico{width:44px;height:44px;border-radius:50%;background:#fbe9ea;display:flex;align-items:center;justify-content:center;flex:none}
.info strong{display:block;font-weight:600;color:var(--ink);margin-top:6px}

.footer{left:0;top:2709px;width:1200px;height:200px;background:var(--footer-bg)}
.foot-brand{left:268px;top:2752px;font-size:11px;color:var(--ink)}
.foot-label{top:2755px;font-size:9px;color:#999;letter-spacing:.5px}
.foot-col{top:2783px;font-size:9px;line-height:14px;color:#444}
.foot-col a{display:block;text-decoration:underline}
.foot-line{left:126px;top:2860px;width:899px;height:1px;background:var(--line)}
.copy{left:0;top:2878px;width:1200px;text-align:center;font-size:9px;color:#444}
</style>
</head>
<body>

<header>
  <div class="abs hero"></div>
  <nav class="abs nav">
    <span class="active">Die Argentur</span><span>Refernzen</span><span>Engagement</span><span>Aktuelles</span><span>Kontakt</span><span>FAQ</span>
  </nav>
  <div class="abs social" aria-label="Soziale Netzwerke"><span></span><span></span><span></span><span></span></div>
  <div class="abs phone-top">03722 - 480150</div>
  <div class="abs brand">Falkenhainer Webdesign</div>
  <div class="abs tagline">Ideen, die Kreise ziehen</div>
</header>

<section class="services">
  <div class="abs service" style="left:88px;padding-top:38px"><h3>Konzeption &amp; Beratung</h3><p>Wir entwickeln Ihr individuelles Konzept und begleiten Sie über die Fertigstellung hinaus.</p></div>
  <div class="abs service" style="left:349px;padding-top:28px"><h3>Webdesign &amp;<br>Programmierung</h3><p>Wir setzen Ihre individuell gestaltete Webseite mittels aktueller Web-Technologien um.</p></div>
  <div class="abs service" style="left:608px;padding-top:31px"><h3>Online Marketing</h3><p>Wir analysieren Ihre Webseite und schaffen Voraussetzungen für ein optimales Google-Ranking.</p></div>
  <div class="abs service" style="left:868px;padding-top:29px"><h3>Domain &amp; Webhosting</h3><p>Alles was Sie für Ihr Webprojekt brauchen.</p></div>
</section>

<section class="about">
  <h2 class="abs section-title" style="top:657px">Falkenhainer Webdesign – Ihr Partner<br>für außergewöhnliche Onlinepräsenzen</h2>
  <div class="abs rule" style="top:740px;width:553px"></div>
  <p class="abs lead">Wir bieten seit mehr als 16 Jahren Internetauftritte für kleine und mittelständische Unternehmen an.</p>
  <p class="abs body-copy" style="top:831px">Als Full-Service-Internetagentur liefern wir Ihnen individuelle auf Ihre Bedürfnisse, Ihre Branche und Ihre Zielgruppe zugeschnittene Lösungen für Ihre Onlinepräsentation an. Unser Angebot beinhaltet sowohl ein ideenreiches Webdesign kombiniert mit den aktuellsten Grundsätzen für Web-Programmierung als auch die Unterstützung für Ihr erfolgreiches Werben im Internet.</p>
  <p class="abs body-copy" style="top:879px">Eine gute Beratung heißt für uns genau hinhören und verstehen, was Sie wirklich brauchen. Je besser wir Ihre Ziele kennen, desto besser können wir Ihre Onlinepräsenz umsetzen. Unsere Kundenberater erläutern Ihnen persönlich mit Enthusiasmus die verschiedenen Möglichkeiten der Darstellung Ihrer Firma im Internet und entwickeln Konzepte, die Ihren Anforderungen bestmöglich entsprechen. Nicht nur während der Projektphase, sondern auch nach Onlinestellung Ihrer Internetseite stehen wir Ihnen mit persönlicher Kundenbetreuung und Supportdienstleistungen zur Verfügung.</p>
  <p class="abs body-copy" style="top:944px">Überzeugen Sie sich von uns und unseren Referenzen und vereinbaren Sie einen Termin unter 03722 480150 oder schreiben Sie uns an <a href="#">info@falkenhainer-webdesign.example</a>, gern auch über unser Kontaktformular.</p>
</section>

<section class="clients">
  <h2 class="abs section-title" style="top:1008px">Unsere zufriedenen Kunden</h2>
  <div class="abs rule" style="top:1049px;width:393px"></div>

  <div class="abs tile" style="left:88px;top:1105px;width:498px;height:564px;background:var(--tile-blue)">
    <span class="abs badge">NEU</span>
    <span class="tile-name" style="font-size:24px;color:#1a8fcc;font-weight:600">Steuerhilfe Ringbach e.V.</span>
  </div>
  <div class="abs tile" style="left:612px;top:1105px;width:498px;height:269px;background:var(--tile-orange)">
    <span class="tile-name" style="font-size:44px;color:#fff;font-weight:700">KWR</span>
  </div>
  <div class="abs tile" style="left:610px;top:1400px;width:236px;height:269px;background:var(--tile-sand)">
    <span class="tile-name" style="font-size:17px;color:#5c4a1e;font-weight:700">Gartenholz Brandt</span>
  </div>
  <div class="abs tile" style="left:872px;top:1400px;width:238px;height:122px;background:var(--tile-navy);gap:10px">
    <span class="tile-name" style="font-size:11px;color:#fff;font-weight:600;line-height:14px">Dachdeckermeister<br>Jonas Keller</span>
    <span style="width:24px;height:24px;border-radius:50%;background:#fff;display:block"></span>
  </div>
  <div class="abs tile" style="left:872px;top:1548px;width:238px;height:121px;background:var(--tile-lilac)">
    <span class="tile-name" style="font-size:20px;color:#6b3d86;font-weight:700">Busreisen Lorenz</span>
  </div>

  <div class="abs carousel">
    <svg width="12" height="18" viewBox="0 0 12 18"><path d="M10 2 3 9l7 7" fill="none" stroke="#d81f2a" stroke-width="3" stroke-linecap="round"/></svg>
    <span class="dot on"></span><span class="dot"></span><span class="dot"></span><span class="dot"></span><span class="dot"></span>
    <svg width="12" height="18" viewBox="0 0 12 18"><path d="m2 2 7 7-7 7" fill="none" stroke="#d81f2a" stroke-width="3" stroke-linecap="round"/></svg>
  </div>
</section>

<section class="news-list">
  <h2 class="abs section-title" style="top:1778px">Was es neues gibt</h2>
  <div class="abs rule" style="top:1818px;width:257px"></div>
  <article class="abs news" style="left:88px;width:320px">
    <time>10.09.2019</time><h4>"Für jeden" ETWAS bei Falkenhainer Webdesign</h4>
    <p>Unsere Aufgabe war der Websiten-Relaunch, ab sofort erstrahlt die Homepage im neuem Glanz...</p><a href="#">Weiter Lesen</a>
  </article>
  <article class="abs news" style="left:444px;width:319px">
    <time>12.04.2019</time><h4>Malerprojekt Ringbach GmbH</h4>
    <p>Erstellung der Website, welche im klassischen Stil Unternehmen, Philosophie und das Leistungsspektrum</p><a href="#">Weiter Lesen</a>
  </article>
  <article class="abs news" style="left:787px;width:322px">
    <time>02.10.2019</time><h4 class="wrap">ACHTUNG - eingeschränkten Verfügbarkeit von HostedMail-Konten</h4>
    <p>Have you ever finally just gave in to the temptation and read your horoscope in the newspaper on Sunday morning? Sure, we</p><a href="#">Weiter Lesen</a>
  </article>
</section>

<section class="contact">
  <h2 class="abs section-title" style="top:2091px">Wir haben Ihr Interesse geweckt?</h2>
  <div class="abs rule" style="top:2131px;width:470px"></div>

  <div class="abs kicker">Einfach und dierekt</div>
  <h3 class="abs form-title" style="font-weight:400">Schreiben Sie uns</h3>
  <p class="abs form-intro">Gerne können sie uns hier eine Mail mit fragen, anfragen oder was Sie uns mitteilen möchten</p>
  <div class="abs field" style="top:2328px">vor und zuname</div>
  <div class="abs field" style="top:2367px">E-Mail Adresse</div>
  <div class="abs field" style="top:2406px;width:224px">Adresse</div>
  <div class="abs field" style="top:2406px;left:320px;width:72px;text-align:center;padding-left:0;padding-right:0">PLZ</div>
  <div class="abs field" style="top:2445px">Telefonnummer</div>
  <div class="abs field" style="top:2482px;height:120px;border-radius:12px">Ihre Anfrage</div>
  <div class="abs submit">Senden</div>

  <div class="abs map" role="img" aria-label="Stadtplan mit Standort des Büros"></div>

  <div class="abs info" style="left:532px;top:2503px">
    <span class="ico"><svg width="18" height="18" viewBox="0 0 18 18" fill="none" stroke="#d81f2a" stroke-width="1.6"><path d="M3 11V9a6 6 0 0 1 12 0v2"/><rect x="2" y="10" width="3" height="5" rx="1"/><rect x="13" y="10" width="3" height="5" rx="1"/></svg></span>
    <div><strong>Unsere Nummer</strong>03722 - 480150</div>
  </div>
  <div class="abs info" style="left:707px;top:2503px">
    <span class="ico"><svg width="18" height="18" viewBox="0 0 18 18" fill="none" stroke="#d81f2a" stroke-width="1.6"><circle cx="9" cy="9" r="7"/><path d="M9 5v4l3 2"/></svg></span>
    <div><strong>Unsere Arbeitzeiten</strong>Mo - Fr, 08:30 - 17:00</div>
  </div>
  <div class="abs info" style="left:908px;top:2503px">
    <span class="ico"><svg width="18" height="18" viewBox="0 0 18 18" fill="none" stroke="#d81f2a" stroke-width="1.6"><path d="M2 3h14v9H8l-4 3v-3H2z"/></svg></span>
    <div><strong>Email</strong>info@falkenhainer-webdesign.example</div>
  </div>
  <div class="abs info" style="left:532px;top:2593px">
    <span class="ico"><svg width="18" height="18" viewBox="0 0 18 18" fill="none" stroke="#d81f2a" stroke-width="1.6"><circle cx="9" cy="6" r="3"/><path d="M9 9v7"/></svg></span>
    <div><strong>Unser Büro</strong>Lindenweg 12,<br>09123 Falkenhain</div>
  </div>
</section>

<footer>
  <div class="abs footer"></div>
  <div class="abs foot-brand">Falkenhainer Webdesign</div>
  <div class="abs foot-label" style="left:451px">LINKS</div>
  <div class="abs foot-col" style="left:451px"><a href="#">Portfolio</a><a href="#">Die Agentur</a><a href="#">Referenzen</a><a href="#">Aktuelles</a></div>
  <div class="abs foot-col" style="left:554px"><a href="#">Kontakt</a><a href="#">FAQ</a><a href="#">Impressum</a><a href="#">Datenschutz</a></div>
  <div class="abs foot-label" style="left:694px">INFO</div>
  <div class="abs foot-col" style="left:694px">Falkenhainer Webdesign<br>Inh. Carla Meinert<br>Lindenweg 12<br>09123 Falkenhain</div>
  <div class="abs foot-col" style="left:831px">Fon: 03722 - 480150<br>Fax: 03722 - 480159<br><a href="#">info@falkenhainer-webdesign.example</a></div>
  <div class="abs foot-line"></div>
  <div class="abs copy">© 2019 Falkenhainer Webdesign</div>
</footer>

</body>
</html>
```